Firm Stationery Design

I need a design for stationery, including: Stationery First Page, Stationery Second Sheet, Envelope, Mailing Label for Flat Envelopes, and Business Cards

```html
<!DOCTYPE html>
<html lang="en">
<head>
<meta charset="utf-8">
<title>Harlow Law LLC — Business Cards</title>
<link rel="stylesheet" href="https://fonts.googleapis.com/css2?family=Montserrat:wght@400;500;700;800&display=swap">
<style>
  :root {
    --backdrop: #2a2a2a;
    --card: #161616;
    --ink: #ffffff;
    --accent: #f59f1e;
    --accent-muted: #c98a2e;
    --pattern-dark: #0e0e0e;
    --pattern-mid: #3a3a3a;
    --pattern-light: #c8c8c8;
  }
  * { box-sizing: border-box; margin: 0; padding: 0; }
  html, body {
    width: 1200px; height: 689px; overflow: hidden;
    background: var(--backdrop);
    font-family: "Montserrat", sans-serif;
  }
  .stage {
    position: relative; width: 1200px; height: 689px;
  }
  .card {
    position: absolute; top: 196px;
    width: 520px; height: 297px;
    border-radius: 18px;
    background: var(--card);
    overflow: hidden;
  }
  .card--back { left: 50px; }
  .card--front { left: 630px; }

  .back-pattern {
    position: absolute; inset: 0;
    background: linear-gradient(100deg, var(--pattern-dark) 0%, var(--pattern-mid) 50%, var(--pattern-light) 100%);
  }
  .back-brand {
    position: absolute; left: 50%; top: 50%;
    transform: translate(-50%, -50%);
    display: flex; align-items: center; gap: 12px;
    background: var(--card);
    padding: 14px 22px; border-radius: 4px;
  }
  .brand-square { width: 26px; height: 26px; background: var(--accent); }
  .brand-name {
    font-weight: 800; font-size: 26px; color: var(--ink); letter-spacing: 1px;
  }

  .front-brand {
    position: absolute; left: 44px; top: 0; bottom: 0; width: 200px;
    display: flex; flex-direction: column; justify-content: center;
  }
  .front-brand .brand-square { width: 54px; height: 54px; margin-bottom: 18px; }
  .front-brand .brand-name { font-size: 40px; line-height: 1; letter-spacing: 1px; }
  .brand-tagline {
    margin-top: 10px; font-weight: 700; font-size: 14px;
    letter-spacing: 9px; color: var(--accent-muted);
  }
  .divider {
    position: absolute; left: 262px; top: 58px; width: 1.5px; height: 180px;
    background: var(--accent);
  }
  .contact {
    position: absolute; left: 284px; top: 58px; right: 20px;
    color: var(--ink); font-size: 11.5px; line-height: 1.55;
  }
  .contact-name { color: var(--accent); font-weight: 800; font-size: 19px; line-height: 1.1; }
  .contact-role { font-size: 12.5px; margin-bottom: 12px; }
  .contact-address { margin-bottom: 12px; }
  .contact-line { display: flex; align-items: center; gap: 8px; }
  .contact-line svg { width: 11px; height: 11px; flex: none; fill: var(--accent); }
</style>
</head>
<body>
<main class="stage">
  <section class="card card--back" aria-label="Business card back">
    <div class="back-pattern" role="img" aria-label="Repeating chevron pattern fading from black to silver"></div>
    <div class="back-brand">
      <span class="brand-square"></span>
      <span class="brand-name">HARLOW</span>
    </div>
  </section>

  <section class="card card--front" aria-label="Business card front">
    <div class="front-brand">
      <span class="brand-square"></span>
      <span class="brand-name">HARLOW</span>
      <span class="brand-tagline">LAW LLC</span>
    </div>
    <div class="divider"></div>
    <div class="contact">
      <p class="contact-name">DANIEL MARSH</p>
      <p class="contact-role">Managing Director</p>
      <p class="contact-address">Your address, City<br>State, Zip 1234</p>
      <p class="contact-line">
        <svg viewBox="0 0 24 24"><path d="M6.6 10.8a15 15 0 0 0 6.6 6.6l2.2-2.2a1 1 0 0 1 1-.25 11.4 11.4 0 0 0 3.6.57 1 1 0 0 1 1 1V20a1 1 0 0 1-1 1A17 17 0 0 1 3 4a1 1 0 0 1 1-1h3.5a1 1 0 0 1 1 1c0 1.25.2 2.45.57 3.57a1 1 0 0 1-.25 1z"/></svg>
        123 456 789
      </p>
      <p class="contact-line">
        <svg viewBox="0 0 24 24"><path d="M2 5h20v14H2z M2 5l10 8 10-8" /></svg>
        info@yourmail.com
      </p>
      <p class="contact-line">
        <svg viewBox="0 0 24 24"><circle cx="12" cy="12" r="10"/></svg>
        www.yourwebsite.com
      </p>
    </div>
  </section>
</main>
</body>
</html>
```